Business Card Design Project

We need a Business Card for an Mechanical Engineering firm in Singapore. The design should be Modern & Technical looking, yet eye catching.

Our company deals in Cutting Tools & Machine Accessories for the Manufacturing Industries such as Oil & Gas, Aero Space, etc... For more information on our Company, you can either email me or view our website www.torvalen.com.sg.

We are trying to revamp our image to give our consumers a fresh new perspective to our company, so we welcome all ideas.

Industry/Entity Type

Business

Requirements
Must have
• Must incorporate New Company Logo into the card as shown in Uploaded file.

```html
<!DOCTYPE html>
<html lang="en">
<head>
<meta charset="utf-8">
<title>Torvalen Tools – Business Card</title>
<link href="https://fonts.googleapis.com/css2?family=Arimo:wght@400;700&display=swap" rel="stylesheet">
<style>
  :root {
    --page: #e9e9ea;
    --card-dark: #231f20;
    --card-dark-2: #2e2a2b;
    --brand-red: #a6252b;
    --brand-red-dark: #861b20;
    --silver-light: #f4f4f5;
    --silver-mid: #d3d4d6;
    --silver-dark: #b4b6b9;
    --ink-white: #ffffff;
    --ink-dark: #3a3637;
  }
  * { box-sizing: border-box; margin: 0; padding: 0; }
  html, body { width: 1200px; height: 944px; overflow: hidden; }
  body {
    background: var(--page);
    font-family: "Arimo", Arial, sans-serif;
    position: relative;
  }
  .card {
    position: absolute;
    width: 600px;
    height: 343px;
    border-radius: 18px;
    overflow: hidden;
    box-shadow: 0 10px 28px rgba(0,0,0,0.22);
  }
  /* Front side */
  .card-front {
    left: 110px; top: 80px;
    background: linear-gradient(160deg, var(--card-dark-2), var(--card-dark));
    border-bottom: 6px solid var(--brand-red);
  }
  .brand-lockup {
    position: absolute;
    left: 0; right: 0; top: 120px;
    display: flex; align-items: center; justify-content: center; gap: 16px;
  }
  .brand-dot {
    width: 38px; height: 38px; border-radius: 50%;
    background: var(--brand-red);
  }
  .brand-name {
    font-weight: 700;
    font-size: 46px;
    letter-spacing: 1px;
    color: var(--ink-white);
  }
  .front-web {
    position: absolute;
    left: 0; right: 0; top: 258px;
    text-align: center;
    color: var(--ink-white);
    font-size: 19px;
    letter-spacing: 1px;
  }
  /* Back side */
  .card-back {
    left: 490px; top: 500px;
    display: flex;
  }
  .back-info {
    width: 52%;
    background: linear-gradient(180deg, #b12a30, var(--brand-red-dark));
    color: var(--ink-white);
    padding: 38px 0 0 40px;
  }
  .person-name { font-size: 24px; }
  .person-role { font-size: 15px; margin-top: 4px; }
  .address {
    display: flex; gap: 10px; margin-top: 42px;
    font-size: 16px; line-height: 1.3;
  }
  .contact-list { list-style: none; margin-top: 18px; }
  .contact-list li {
    display: flex; align-items: center; gap: 10px;
    font-size: 16px; line-height: 1.45;
  }
  .icon { width: 14px; height: 14px; flex: none; fill: var(--ink-white); }
  .back-brand {
    width: 48%;
    background: linear-gradient(135deg, var(--silver-light), var(--silver-mid) 55%, var(--silver-dark));
    display: flex; align-items: center; justify-content: center; gap: 10px;
  }
  .back-brand .brand-name { font-size: 28px; color: var(--ink-dark); }
  .back-brand .brand-dot { width: 22px; height: 22px; }
</style>
</head>
<body>

<section class="card card-front" aria-label="Business card front">
  <div class="brand-lockup">
    <span class="brand-dot"></span>
    <span class="brand-name">TORVALEN TOOLS</span>
  </div>
  <p class="front-web">www.torvalentools.com</p>
</section>

<section class="card card-back" aria-label="Business card back">
  <div class="back-info">
    <p class="person-name">Marcus Lindqvist</p>
    <p class="person-role">director</p>
    <div class="address">
      <svg class="icon" viewBox="0 0 14 14" aria-hidden="true"><path d="M7 1 L13 7 H11 V13 H8 V9 H6 V13 H3 V7 H1 Z"/></svg>
      <p>1840 Halden Crest Rd.<br>Marlow, TX 78114</p>
    </div>
    <ul class="contact-list">
      <li><svg class="icon" viewBox="0 0 14 14" aria-hidden="true"><path d="M3 1 L5 1 L6 4 L4.5 5.5 C5.3 7.3 6.7 8.7 8.5 9.5 L10 8 L13 9 L13 11 C13 12 12 13 11 13 C5.5 13 1 8.5 1 3 C1 2 2 1 3 1 Z"/></svg>512-004-3920</li>
      <li><svg class="icon" viewBox="0 0 14 14" aria-hidden="true"><path d="M4 0.5 H10 A1 1 0 0 1 11 1.5 V12.5 A1 1 0 0 1 10 13.5 H4 A1 1 0 0 1 3 12.5 V1.5 A1 1 0 0 1 4 0.5 Z M4.5 2 V10.5 H9.5 V2 Z"/></svg>512-004-3921</li>
      <li><svg class="icon" viewBox="0 0 14 14" aria-hidden="true"><path d="M1 3 H13 V11 H1 Z M1.5 3.5 L7 8 L12.5 3.5" stroke="#a6252b" stroke-width="1"/></svg>info@torvalentools.com</li>
      <li><svg class="icon" viewBox="0 0 14 14" aria-hidden="true"><circle cx="7" cy="7" r="6"/></svg>www.torvalentools.com</li>
    </ul>
  </div>
  <div class="back-brand">
    <span class="brand-dot"></span>
    <span class="brand-name">TORVALEN TOOLS</span>
  </div>
</section>

</body>
</html>
```